Label design for olive oil and other oils

We are a company located in Melbourne, doing the international trade, now we are starting a olive oil project and need a label for our product. Our olive oil named "Blue Heron", our products is produce in Australia and will export oversea, The label should be brief and clear. We offer the natural and premium products to our customers. The bottles of the oil will be 500ml, 750ml and 1L. Our label will use for other kinds of oil in the future, such as the nut oil, almond oil and macadamia oil, so we would like the design can be expand to other oil as well, so a series of oil label will be welcomed.

Target Market(s)

Australia local market and oversea.

Industry/Entity Type

Food Store

Requirements
Must have
• none
Nice to have
• The blue heron bird
Should not have
• none

```html
<!DOCTYPE html>
<html lang="en">
<head>
<meta charset="utf-8">
<title>Blue Heron Extra Virgin Olive Oil – Label Set</title>
<link rel="stylesheet" href="https://fonts.googleapis.com/css2?family=Arvo:wght@400;700&family=Courier+Prime:wght@400;700&display=swap">
<style>
  :root{
    --paper:#ffffff;
    --cream:#f3f0d4;
    --frame:#8b8a4c;
    --ink:#5a592d;
    --olive:#a3ac3c;
    --leaf-dark:#5f8a2a;
    --caption:#555555;
  }
  *{margin:0;padding:0;box-sizing:border-box;}
  html,body{width:807px;height:1200px;overflow:hidden;background:var(--paper);}
  body{position:relative;font-family:"Courier Prime",monospace;color:var(--ink);}

  .caption{position:absolute;top:112px;font-family:Arial,Helvetica,sans-serif;font-size:17px;color:var(--caption);}
  .caption--front{left:94px;}
  .caption--back{left:425px;}

  .label{position:absolute;top:148px;width:283px;height:960px;background:var(--cream);
    border:3px solid var(--frame);border-radius:18px;}
  .label--front{left:94px;}
  .label--back{left:425px;}

  /* front */
  .artwork-birds{position:absolute;left:72px;top:26px;width:136px;height:92px;border-radius:46px;
    background:radial-gradient(ellipse at center,#c58a6e 0%,#b6533f 45%,rgba(243,240,212,0) 72%);}
  .brand-name{position:absolute;left:0;right:0;top:175px;text-align:center;
    font-family:"Courier Prime",monospace;font-weight:700;font-size:40px;line-height:1;color:var(--ink);white-space:nowrap;}
  .origin{position:absolute;top:268px;left:0;right:0;text-align:center;font-family:"Arvo",serif;font-size:15px;color:var(--ink);}
  .grade{position:absolute;left:0;right:0;text-align:center;font-family:"Courier Prime",monospace;font-weight:700;color:var(--ink);line-height:1;}
  .grade--extra{top:300px;font-size:52px;}
  .grade--virgin{top:352px;font-size:50px;}
  .product-band{position:absolute;left:19px;top:420px;width:243px;height:56px;background:var(--olive);
    border-radius:4px;display:flex;align-items:center;justify-content:center;
    font-family:"Arvo",serif;font-weight:700;font-size:34px;color:var(--cream);}
  .flavour{position:absolute;top:486px;left:0;right:0;text-align:center;font-family:"Arvo",serif;font-size:17px;color:var(--ink);}
  .artwork-branch{position:absolute;left:40px;top:535px;width:200px;height:330px;border-radius:50%;
    background:radial-gradient(ellipse at center,#b7d657 0%,#9cc33a 40%,rgba(243,240,212,0) 70%);}
  .volume{position:absolute;top:895px;left:0;right:0;text-align:center;font-family:"Arvo",serif;font-size:26px;color:var(--ink);}

  /* back */
  .story{position:absolute;left:14px;right:14px;top:20px;text-align:center;font-size:14.5px;line-height:22px;
    font-weight:700;color:var(--ink);text-transform:uppercase;}
  .rule{position:absolute;left:14px;right:14px;height:2px;background:var(--frame);}
  .rule--a{top:214px;}
  .rule--b{top:408px;}
  .rule--c{top:450px;}
  .benefits{position:absolute;left:18px;top:226px;list-style:none;}
  .benefits li{display:flex;align-items:center;height:29px;font-size:13px;font-weight:700;}
  .benefits svg{width:18px;height:18px;margin-right:10px;flex:none;}
  .storage{position:absolute;left:14px;right:14px;top:414px;text-align:center;font-size:12px;line-height:15px;font-weight:700;}
  .nutrition-title{position:absolute;left:18px;top:455px;font-size:12.5px;font-weight:700;}
  .nutrition{position:absolute;left:18px;top:474px;width:244px;border-collapse:collapse;font-size:9.5px;line-height:13.5px;}
  .nutrition td{padding:0 2px;border-bottom:1px solid rgba(139,138,76,.35);}
  .nutrition td:nth-child(2),.nutrition td:nth-child(3),.nutrition td:nth-child(4){text-align:right;}
  .notes{position:absolute;left:18px;width:150px;top:640px;font-size:9px;line-height:11.5px;text-transform:uppercase;}
  .producer{position:absolute;left:18px;right:18px;top:762px;font-size:9px;line-height:11.5px;text-transform:uppercase;}
  .net{position:absolute;left:18px;right:18px;top:805px;font-size:9px;line-height:11.5px;}
</style>
</head>
<body>
  <p class="caption caption--front">Typ1 Fruity &amp; Aromatic</p>
  <p class="caption caption--back">Back label</p>

  <section class="label label--front">
    <div class="artwork-birds" role="img" aria-label="Illustration of two small birds perched on a branch"></div>
    <div class="brand-name">Blue Heron</div>
    <p class="origin">Products Of Australia</p>
    <div class="grade grade--extra">Extra</div>
    <div class="grade grade--virgin">virgin</div>
    <div class="product-band">Olive Oil</div>
    <p class="flavour">Fruity &amp; Aromatic</p>
    <div class="artwork-branch" role="img" aria-label="Illustration of an olive branch with green olives and leaves"></div>
    <p class="volume">750ml</p>
  </section>

  <section class="label label--back">
    <p class="story">Olives that are cold pressed within 24 hours from harvest of trees grown in rich soils, in a climate of hot summer days and cold winter nights to produce optimum condi-tions to produce world class olive oil.</p>
    <div class="rule rule--a"></div>
    <ul class="benefits">
      <li><svg viewBox="0 0 18 18"><rect x="1" y="1" width="16" height="16" fill="none" stroke="#5f8a2a" stroke-width="1.5"/><path d="M4 9l3.5 3.5L14 5" fill="none" stroke="#5f8a2a" stroke-width="2.4"/></svg>First cold pressed</li>
      <li><svg viewBox="0 0 18 18"><rect x="1" y="1" width="16" height="16" fill="none" stroke="#5f8a2a" stroke-width="1.5"/><path d="M4 9l3.5 3.5L14 5" fill="none" stroke="#5f8a2a" stroke-width="2.4"/></svg>Preservatives</li>
      <li><svg viewBox="0 0 18 18"><rect x="1" y="1" width="16" height="16" fill="none" stroke="#5f8a2a" stroke-width="1.5"/><path d="M4 9l3.5 3.5L14 5" fill="none" stroke="#5f8a2a" stroke-width="2.4"/></svg>100% Natural product</li>
      <li><svg viewBox="0 0 18 18"><rect x="1" y="1" width="16" height="16" fill="none" stroke="#5f8a2a" stroke-width="1.5"/><path d="M4 9l3.5 3.5L14 5" fill="none" stroke="#5f8a2a" stroke-width="2.4"/></svg>No GMO</li>
      <li><svg viewBox="0 0 18 18"><rect x="1" y="1" width="16" height="16" fill="none" stroke="#5f8a2a" stroke-width="1.5"/><path d="M4 9l3.5 3.5L14 5" fill="none" stroke="#5f8a2a" stroke-width="2.4"/></svg>100% Australian grown</li>
      <li><svg viewBox="0 0 18 18"><rect x="1" y="1" width="16" height="16" fill="none" stroke="#5f8a2a" stroke-width="1.5"/><path d="M4 9l3.5 3.5L14 5" fill="none" stroke="#5f8a2a" stroke-width="2.4"/></svg>Natural antioxidants</li>
    </ul>
    <div class="rule rule--b"></div>
    <p class="storage">STORE AWAY FROM DIRECT SUNLIGHT AT ROOM TEMPERATURE</p>
    <div class="rule rule--c"></div>
    <p class="nutrition-title">NUTRITIONAL INFORMATION</p>
    <table class="nutrition">
      <tr><td>Serving</td><td>kJ/100ml</td><td>Serve</td><td>%DI</td></tr>
      <tr><td>Energy</td><td>3400</td><td>476</td><td>5.5</td></tr>
      <tr><td>Protein</td><td>0</td><td>0</td><td>0</td></tr>
      <tr><td>Total Fat</td><td>92</td><td>12.9</td><td>18</td></tr>
      <tr><td>-Saturated</td><td>14</td><td>2.0</td><td>8.1</td></tr>
      <tr><td>-Polyunsaturated</td><td>10</td><td>1.4</td><td>&nbsp;</td></tr>
      <tr><td>-Monounsaturated</td><td>68</td><td>9.5</td><td>&nbsp;</td></tr>
      <tr><td>Carbohydrate</td><td>0</td><td>0</td><td>0</td></tr>
      <tr><td>-Sugars</td><td>0</td><td>0</td><td>0</td></tr>
      <tr><td>Sodium</td><td>0</td><td>0</td><td>0</td></tr>
    </table>
    <p class="notes">Total polyphenols as basic olive leaf extract not less than 250mg per kg. Ideal for salads, dressings and light cooking. Product of Australia.</p>
    <p class="producer">Produced by: Southgate Grove Traders Pty Ltd<br>18 Wattle Lane, Kingsford VIC 3000, Australia</p>
    <p class="net">Blue Heron Extra Virgin Olive Oil<br>500 ML / 16.9 FLOZ</p>
  </section>
</body>
</html>
```